New Product = Home Water Infiltration Solution!

We are launching a new product to the construction industry that will eliminate water infiltration for homeowners. Our new product, Brell Edge Divertor Trim will revolutionize the industry. We want to convey to builders and homeowners the importance of the product by showing images of rotted side walls (mold, moisture, rot, and algae) on a home. Rotted Side walls are due to there being no industry standard on how to properly install a kickout. Our new product brings uniformity to the industry and are easy to install for roofers and sider's. I also want to show pictures of our product installed on a home to convey the ease of install and that it is aesthetically pleasing on a home. I have attached pictures of rotted walls that have rotted due to water infiltrating under the siding. I've attached pictures of our Brell edge Divertor installed on a home. Also, I have attached jpgs of former marketing pieces we have used for reference and out logo. We are looking to create a piece that is eye catching, informative, generated the need to know more, and professional. Please feel free to check out our website for futher information as well as our Youtube page. www.americanflashings.comYouTube Link - https://www.youtube.com/channel/UCHNrw7Tpy3Y2yVU6At96KEwThings to include:Our LogoPhone (231)834-5905www.americanflashings.com1845 Newaygo RdBailey MI 49303

Target Market(s)

Home and/or Construction Tradesmen/women that specialize in the exteriors, home/building inspectors, Home/commerical builders, Home/Commercial exterior installers, Roofing Contractors, Siding Contractors, Building Supply Wholesalers.

Colors

Designer to choose colors to be used in the design.

Requirements
Must have
• pictures of homes that have been ruined by water getting behind the siding or roofing and rotting away at the side walls.
Nice to have
• Website
• Find us on Youtube
• Eye Catching design

```html
<!DOCTYPE html>
<html lang="en">
<head>
<meta charset="utf-8">
<title>Brell Edge Divertor Trim Flyer</title>
<link href="https://fonts.googleapis.com/css2?family=Montserrat:wght@600;700;800;900&display=swap" rel="stylesheet">
<style>
  :root {
    --orange: #f47b20;
    --charcoal: #2b2b2d;
    --black: #111111;
    --white: #ffffff;
    --ink: #1a1a1a;
    --backdrop: #e6e6e4;
    --siding-blue: #6f8fb4;
    --rot-brown: #6b5a3a;
    --trim-grey: #d9d8d2;
  }
  * { box-sizing: border-box; margin: 0; padding: 0; }
  html, body { width: 1200px; height: 794px; overflow: hidden; }
  body {
    background: var(--backdrop);
    font-family: "Montserrat", sans-serif;
    position: relative;
  }
  .flyer {
    position: absolute;
    left: 330px; top: 15px;
    width: 540px; height: 764px;
    background: var(--white);
    overflow: hidden;
    box-shadow: 0 6px 18px rgba(0,0,0,.18);
  }
  .flyer-shapes { position: absolute; inset: 0; }
  .headline {
    position: absolute; left: 30px; top: 26px;
    color: var(--white);
    font-weight: 900; font-size: 40px; line-height: 1.05;
    text-transform: uppercase; letter-spacing: .5px;
    text-shadow: 3px 3px 0 var(--charcoal);
  }
  .photo {
    position: absolute; border-radius: 50%;
    border: 4px solid var(--white);
  }
  .photo--siding { left: 26px; top: 250px; width: 240px; height: 240px;
    background: radial-gradient(circle at 35% 35%, #c9d6e4, var(--siding-blue) 70%); }
  .photo--rot-corner { left: 262px; top: 172px; width: 110px; height: 110px;
    background: radial-gradient(circle at 40% 40%, #b59a5c, var(--rot-brown)); }
  .photo--mold-wall { left: 362px; top: 135px; width: 150px; height: 150px;
    background: radial-gradient(circle at 50% 40%, #9aa58a, #4e4a3a); }
  .photo--installed { left: 350px; top: 262px; width: 130px; height: 130px;
    background: radial-gradient(circle at 50% 50%, #d8d3cc, #6e5f58); }
  .benefits {
    position: absolute; left: 318px; top: 408px; width: 210px;
    list-style: none;
    color: var(--orange); font-weight: 700; font-size: 12px; line-height: 1.35;
  }
  .benefits li { padding-left: 12px; position: relative; }
  .benefits li::before { content: "•"; position: absolute; left: 0; }
  .product-shot {
    position: absolute; right: 18px; bottom: 92px; width: 150px; height: 100px;
    border-radius: 6px;
    background: linear-gradient(135deg, #f4f3ef, var(--trim-grey));
  }
  .brand {
    position: absolute; left: 30px; top: 505px;
    display: flex; align-items: center; gap: 10px;
  }
  .brand-mark { width: 22px; height: 22px; background: var(--orange); flex: none; }
  .brand-name { font-weight: 900; font-size: 20px; line-height: 1.1; color: var(--ink); text-transform: uppercase; }
  .problems {
    position: absolute; left: 30px; top: 568px; width: 255px;
    list-style: none;
    color: var(--ink); font-weight: 800; font-size: 12px; line-height: 1.3;
    text-transform: uppercase;
  }
  .problems li { padding-left: 12px; position: relative; }
  .problems li::before { content: "•"; position: absolute; left: 0; }
  .footer {
    position: absolute; left: 0; right: 0; bottom: 0; height: 72px;
    background: var(--black); color: var(--white);
    border-top: 6px solid var(--white);
    padding: 14px 30px; font-weight: 700; font-size: 14px; line-height: 1.35;
  }
</style>
</head>
<body>
  <main class="flyer">
    <svg class="flyer-shapes" viewBox="0 0 540 764" aria-hidden="true">
      <rect width="540" height="764" fill="var(--white)"/>
      <rect y="130" width="540" height="570" fill="var(--charcoal)"/>
      <path d="M0,0 H540 V140 C420,180 300,240 0,250 Z" fill="var(--orange)"/>
      <path d="M0,470 C230,470 330,560 390,700 L0,700 Z" fill="var(--white)"/>
    </svg>

    <h1 class="headline">Brell Edge<br>Divertor Trim</h1>

    <div class="photo photo--siding" role="img" aria-label="Photo of blue vinyl siding and roof edge with divertor trim installed"></div>
    <div class="photo photo--rot-corner" role="img" aria-label="Photo of rotted wall corner under a roof edge"></div>
    <div class="photo photo--mold-wall" role="img" aria-label="Photo of moldy sheathing exposed behind removed siding"></div>
    <div class="photo photo--installed" role="img" aria-label="Photo of divertor trim installed where roof meets wall"></div>

    <ul class="benefits">
      <li>Unique patent-pending design</li>
      <li>Diverts water away from sliding and wall</li>
      <li>Roofing and siding install friendly with built-in 3-channel</li>
      <li>Multiple color options</li>
      <li>Saves homes from mold and hidden rotting</li>
    </ul>

    <div class="product-shot" role="img" aria-label="Product photo of the white divertor trim piece"></div>

    <div class="brand">
      <span class="brand-mark"></span>
      <span class="brand-name">Norva<br>Trimworks</span>
    </div>

    <ul class="problems">
      <li>Rotten walls is less than 2 years on this home!</li>
      <li>Ineffective homemade kickout flashing was used</li>
      <li>Leaking window</li>
      <li>Interior damage</li>
      <li>Exterior damage</li>
    </ul>

    <footer class="footer">
      <p>Ph: (555)472-1908 | www.norvatrimworks.com</p>
      <p>2716 Pellham Rd, Corvale MI 49871</p>
    </footer>
  </main>
</body>
</html>
```